LANTERN - and the quiet crafts of everyday life

I´m writing a book about CHANGE and the skills leaders needs to embody the transformation from being amanager to become leaders.
The title of the book in Icelandic is the same as the name of the project (which I want to be used on the designes is:) UPPSPRETTA
(with the subtitle:) og hugrekki hversdagsins

Change is not controlled or managed – Leading effective change is an art form which is one of the big reasons for why 70% of changes within companies fail. The main reason however, is that managers are tasked with managing and directing them. The art form of change is to put it in the hands of leaders who possess the emotional intelligence that is needed – all their other advantages intact – to lead change all the way.

The big problem when it comes to change is that there are too many managers and too few leaders within companies – leaders who possess emotional intelligence which is the most important skill a leader embodies to empower change. A leader has what it takes to empower followership.

A manager tends to push and control, make decisions that he presupposes others to implement the way he expects. An emotionally competent leader leads by example and enhances followership on that journey because of the trust and respect he has earned.

In few words: SOFT SKILLS ARE THE NEW HARD SKILLS!

```html
<!DOCTYPE html>
<html lang="is">
<head>
<meta charset="utf-8">
<title>UPPSPRETTA – og hugrekki hversdagsins</title>
<link rel="stylesheet" href="https://fonts.googleapis.com/css2?family=Archivo+Black&family=Fira+Sans:wght@400&display=swap">
<style>
  :root {
    --cover-top: #b23a3a;
    --cover-mid: #c55440;
    --cover-bottom: #ee9479;
    --title-white: #f2f0ef;
    --title-shade: #dcd8d7;
    --subtitle-red: #6a0e14;
    --rule-light: rgba(255, 225, 215, 0.7);
    --globe-light: #efd2cc;
    --globe-mid: #d98f86;
    --globe-deep: #a8453d;
    --shadow-deep: rgba(120, 28, 22, 0.75);
  }
  html, body {
    margin: 0;
    padding: 0;
    width: 1200px;
    height: 1200px;
    overflow: hidden;
  }
  .book-cover {
    position: relative;
    width: 1200px;
    height: 1200px;
    background:
      linear-gradient(100deg, rgba(255,255,255,0.06) 0%, rgba(0,0,0,0.06) 55%, rgba(255,255,255,0.05) 100%),
      linear-gradient(180deg, var(--cover-top) 0%, var(--cover-mid) 50%, var(--cover-bottom) 100%);
    overflow: hidden;
  }
  .cover-title {
    position: absolute;
    top: 54px;
    left: 0;
    width: 100%;
    margin: 0;
    text-align: center;
    font-family: "Archivo Black", "Arial Black", sans-serif;
    font-size: 128px;
    line-height: 1;
    letter-spacing: -1px;
    background: linear-gradient(180deg, var(--title-white) 0%, var(--title-white) 55%, var(--title-shade) 100%);
    -webkit-background-clip: text;
    background-clip: text;
    color: transparent;
  }
  .cover-artwork {
    position: absolute;
    left: 196px;
    top: 228px;
    width: 800px;
    height: 800px;
    background:
      radial-gradient(circle at 52% 44%, var(--globe-light) 0%, var(--globe-mid) 22%, var(--globe-deep) 37%, rgba(168,69,61,0) 39%),
      radial-gradient(ellipse 46% 14% at 54% 86%, var(--shadow-deep) 0%, rgba(120,28,22,0.45) 60%, rgba(120,28,22,0) 100%);
  }
  .subtitle-band {
    position: absolute;
    left: 258px;
    top: 1052px;
    width: 672px;
    height: 85px;
    border-top: 1px solid var(--rule-light);
    border-bottom: 1px solid var(--rule-light);
    display: flex;
    align-items: center;
    justify-content: center;
  }
  .cover-subtitle {
    margin: 0;
    font-family: "Fira Sans", "Helvetica Neue", sans-serif;
    font-weight: 400;
    font-size: 58px;
    line-height: 1;
    color: var(--subtitle-red);
    white-space: nowrap;
  }
</style>
</head>
<body>
  <main class="book-cover">
    <h1 class="cover-title">UPPSPRETTA</h1>
    <div class="cover-artwork" role="img" aria-label="Illustration: a glowing globe circled by orbit lines, with silhouettes of business people meeting around a table in front of it, casting long shadows"></div>
    <div class="subtitle-band">
      <p class="cover-subtitle">og hugrekki hversdagsins</p>
    </div>
  </main>
</body>
</html>
```